****Business Card Design for Quarrystone Development. Design based around attached logo/company name

I’m looking for business card design for my company Quarrystone Development Group,LLC. Design should be professional, sharp and minimal. Outside of the attached logos, greyscale colors for remainder of cards. My thoughts are two-sided card with attached logo on one side and my info on the other but open to one-sided as well with right design.
Target Market(s)
Real estate professionals including banks, private investors, property owners, developers, commercial tenants like Brewlantern, Grovika or Tanquist’s.
Industry/Entity Type
Commercial real estate development and investments.
Contact Information for Business Card
Name, title, email, phone #’s, web address and physical address
Font styles to use
Other font styles liked:
- Helvetica, Garamond, etc
Colors
Designer to choose only greyscale colors for use in the design.
Requirements
Must have
- Attached logo first or second options.
Nice to have
- Two sided card with logo on one side. Attached Logo/company name can be laid out any way that flows as long as it’s legible.name
Should not have
- No loud colors. ***Please do not include logo, I have removed the company design with a logo image.

```html
<!DOCTYPE html>
<html lang="en">
<head>
<meta charset="utf-8">
<title>Quarrystone Development Group — Business Card</title>
<link href="https://fonts.googleapis.com/css2?family=Cinzel:wght@400;700&family=Arimo:wght@400&display=swap" rel="stylesheet">
<style>
  :root {
    --backdrop: #161616;
    --card: #333334;
    --ink-light: #f2f2f2;
    --ink-mid: #b9b9bb;
    --ink-soft: #8a8a8d;
    --rule: #6c6c6f;
  }
  * { box-sizing: border-box; margin: 0; padding: 0; }
  html, body { width: 1200px; height: 852px; overflow: hidden; }
  body {
    background: var(--backdrop);
    display: flex;
    flex-direction: column;
    align-items: center;
    justify-content: center;
    gap: 40px;
  }
  .card {
    position: relative;
    width: 660px;
    height: 377px;
    background: var(--card);
    box-shadow: 0 10px 30px rgba(0,0,0,.5);
  }

  /* Front */
  .card--front {
    display: flex;
    align-items: center;
    justify-content: center;
  }
  .wordmark {
    display: flex;
    align-items: center;
    gap: 16px;
    font-family: "Cinzel", serif;
    font-weight: 400;
    color: var(--ink-light);
  }
  .wordmark__square {
    width: 22px;
    height: 22px;
    background: var(--ink-mid);
  }
  .wordmark__text { line-height: 1.1; }
  .wordmark__name { font-size: 40px; letter-spacing: 2px; }
  .wordmark__sub { font-size: 15px; letter-spacing: 3px; }

  /* Back */
  .card--back { padding: 0 40px; }
  .card--back .wordmark { position: absolute; left: 40px; top: 96px; gap: 12px; }
  .card--back .wordmark__square { width: 14px; height: 14px; }
  .card--back .wordmark__name { font-size: 26px; letter-spacing: 1.5px; }
  .card--back .wordmark__sub { font-size: 10px; letter-spacing: 2px; }

  .rule {
    position: absolute;
    height: 1px;
    background: var(--rule);
  }
  .rule--top { left: 330px; right: 36px; top: 170px; }
  .rule--bottom { left: 40px; right: 36px; top: 318px; }

  .person {
    position: absolute;
    left: 40px;
    top: 218px;
  }
  .person__name {
    font-family: "Cinzel", serif;
    font-weight: 700;
    font-size: 19px;
    letter-spacing: 1px;
    color: var(--ink-light);
  }
  .person__title {
    font-family: "Arimo", sans-serif;
    font-size: 14px;
    color: var(--ink-light);
    margin-top: 2px;
  }
  .address {
    position: absolute;
    left: 40px;
    top: 290px;
    font-family: "Arimo", sans-serif;
    font-size: 14px;
    color: var(--ink-light);
  }
  .contacts {
    position: absolute;
    left: 40px;
    top: 332px;
    font-family: "Arimo", sans-serif;
    font-size: 13.5px;
    color: var(--ink-light);
    white-space: nowrap;
  }
  .contacts__label, .contacts__sep { color: var(--ink-soft); }
  .contacts__sep { margin: 0 5px; }
</style>
</head>
<body>

  <section class="card card--front" aria-label="Card front">
    <div class="wordmark">
      <span class="wordmark__square"></span>
      <div class="wordmark__text">
        <div class="wordmark__name">QUARRYSTONE</div>
        <div class="wordmark__sub">DEVELOPMENT GROUP, LLC</div>
      </div>
    </div>
  </section>

  <section class="card card--back" aria-label="Card back">
    <div class="wordmark">
      <span class="wordmark__square"></span>
      <div class="wordmark__text">
        <div class="wordmark__name">QUARRYSTONE</div>
        <div class="wordmark__sub">DEVELOPMENT GROUP, LLC</div>
      </div>
    </div>

    <div class="rule rule--top"></div>

    <div class="person">
      <div class="person__name">DANIEL WHITCOMBE</div>
      <div class="person__title">Director</div>
    </div>

    <div class="address">1187 Cedar Ridge Lane Salem, OR 97302</div>

    <div class="rule rule--bottom"></div>

    <div class="contacts">
      <span class="contacts__label">P:</span> (503) 555-0148<span class="contacts__sep">|</span><span class="contacts__label">E:</span> info@quarrystonegroup.com<span class="contacts__sep">|</span><span class="contacts__label">W:</span> www.quarrystonegroup.com
    </div>
  </section>

</body>
</html>
```